Website Design for Chef Wen Chinese Restaurant

Chef Wen is a new Chinese Restaurant. It offers exceptional dining experience with authentic and dynamic dishes created with quality ingredients.

A vivid website theme is required to promote this new restaurant online. Logo, menu, wine list and a few other files are attached for help with designing.

A very rough demo website has been setup and can be accessed via http://www.chefwen.com.au. It is for telling designers what content is shown up on each page (except for homepage). By reading the about us page, designers can get some more info of Chef Wen. However, the layout, theme color, font, etc are not set in stone. Visitors should be able to feel Chef Wen restaurant's authentic Chinese cuisine and high hygiene standard. Home page of the website could be The "Our website is coming soon" description is shown on demo site but do not required to be presented on new design.

Some main pages design should be included: Home (landing page), About us, Menu (Dishes), Winelist, Gallery, Contact us. No HTML and coding required. The output should be well layered psd or png files with acceptable resolution for web use.

A few other website can be referred to are:

http://larkspurasian.com.au/
http://www.river-lamp.com/
http://tamworthy.com.au/
http://harbelrestaurant.com.au/
http://www.quillerestaurant.com.au/
http://www.thekiln.com.au/

Industry/Entity Type

Restaurant

Requirements
Nice to have
• I expect designs of at least these webpages: homepage, menu page and contact us page. If you can provide "about us" page as well, it will probably help you win the competition. well layered psd or png file is my preference.
Should not have
• You don't have to make html/cs/js or any coding. All I need is just art design

```html
<!DOCTYPE html>
<html lang="en">
<head>
<meta charset="utf-8">
<title>Chef Wen Chinese Restaurant</title>
<link rel="stylesheet" href="https://fonts.googleapis.com/css2?family=Roboto:wght@400;500;700&family=Merriweather:wght@400&display=swap">
<style>
:root{
  --red:#ee1111;
  --red-soft:#f03a3a;
  --dark:#231f20;
  --ink:#222;
  --panel:#f2f2f3;
  --white:#fff;
  --rule:#999;
}
*{box-sizing:border-box;margin:0;padding:0}
html,body{width:1092px;height:1200px;overflow:hidden}
body{background:var(--dark);font-family:Roboto,sans-serif;color:var(--ink);position:relative}
.page{position:absolute;left:139px;top:3px;width:815px;height:1136px;background:var(--white)}
.topline{position:absolute;left:139px;top:0;width:825px;height:3px;background:#000}
.brand{position:absolute;left:8px;top:10px;width:170px;text-align:center}
.brand-mark{width:34px;height:34px;border-radius:50%;background:var(--red);margin:0 auto 8px}
.brand-name{font-size:13px;font-weight:700;color:var(--red);line-height:1.2}
.search{position:absolute;left:613px;top:17px;width:156px;height:30px;border:1px solid #bbb;background:#f3f3f3;font-size:10px;padding:9px 11px;color:#333}
.search svg{position:absolute;right:8px;top:7px}
.contact{position:absolute;right:18px;top:63px;text-align:center;font-size:11px;line-height:20px;color:#333}
.nav{position:absolute;left:3px;top:119px;width:809px;height:38px;background:var(--red);display:flex}
.nav a{color:var(--white);font-weight:700;font-size:12px;text-decoration:none;display:flex;align-items:center;justify-content:center;border-right:1px solid #b50000}
.nav a:last-child{border:none}
.hero{position:absolute;left:4px;top:159px;width:807px;height:422px;background:radial-gradient(ellipse at 45% 50%,#d46a48 0%,#e9b590 35%,#ece8e2 65%,#e3e1dc 100%)}
.hero-title{position:absolute;left:304px;top:183px;width:196px;height:46px;background:rgba(60,50,40,.7);color:var(--white);font-size:19px;display:flex;align-items:center;justify-content:center}
.hero-arrow{position:absolute;top:188px}
.dots{position:absolute;left:371px;top:387px;display:flex;gap:2px}
.dots span{width:12px;height:12px;border-radius:50%;border:1.5px solid #333;background:#fff}
.dots span.on{background:radial-gradient(circle,var(--red) 35%,#fff 40%)}
.heading{position:absolute;color:var(--red);font-weight:700;font-size:14px}
.welcome{position:absolute;left:9px;top:618px;width:506px;height:148px;background:var(--panel);padding:10px 13px;font-size:10.8px;line-height:18.5px;color:#333}
.welcome p+p{margin-top:13px}
.tile{position:absolute;width:252px;height:144px}
.tile .cap{position:absolute;left:0;bottom:17px;background:rgba(50,40,35,.7);color:var(--white);font-family:Merriweather,serif;font-size:12.5px;padding:5px 9px;line-height:17px}
.view-all{position:absolute;left:363px;top:1097px;width:154px;height:26px;background:var(--red);color:var(--white);font-family:Merriweather,serif;font-size:11.5px;display:flex;align-items:center;justify-content:center}
.hours{position:absolute;left:537px;top:618px;width:265px;font-size:11px;line-height:17px}
.open-box{display:inline-block;border:1px solid #bbb;padding:8px 11px;font-size:13.5px;margin-bottom:9px}
.hours b{font-weight:500;font-size:11.5px}
.hours .hl{color:var(--red)}
.hours hr{border:none;border-top:1px solid var(--rule);margin:13px 3px 14px 0}
.location{position:absolute;left:539px;top:805px;width:264px;height:316px;background:var(--red-soft);color:var(--white)}
.location h3{font-size:14px;font-weight:500;padding:11px 10px 0}
.map{position:absolute;left:13px;top:37px;width:243px;height:225px;background:linear-gradient(135deg,#d6e4c8,#ece8dc 55%,#e2dfd2)}
.map svg{position:absolute;left:117px;top:130px}
.location .addr{position:absolute;top:276px;width:100%;text-align:center;font-weight:700;font-size:10.8px;line-height:17px}
.footer{position:absolute;top:1152px;left:139px;width:817px;color:var(--white);font-size:10.5px}
.follow{position:absolute;left:0;top:0}
.social{position:absolute;left:0;top:19px;display:flex;gap:3px}
.social span{width:15px;height:15px;background:#3b7fd0}
.fnav{position:absolute;right:0;top:0;word-spacing:2px}
.copy{position:absolute;right:0;top:20px}
</style>
</head>
<body>
<div class="topline"></div>
<div class="page">
  <div class="brand">
    <div class="brand-mark"></div>
    <div class="brand-name">Chef Wen<br>Chinese Restaurant</div>
  </div>
  <div class="search">SEARCH
    <svg width="16" height="16" viewBox="0 0 16 16"><circle cx="6.5" cy="6.5" r="5" fill="none" stroke="#888" stroke-width="1.4"/><line x1="10" y1="10" x2="15" y2="15" stroke="#888" stroke-width="1.6"/></svg>
  </div>
  <div class="contact">3/88 Kendrick Road, Elm Hollow, SA, 5070<br>P : 08 5550 1100 &nbsp;|&nbsp; 08 5550 8878</div>
  <nav class="nav">
    <a style="width:93px">HOME</a><a style="width:115px">ABOUT US</a><a style="width:89px">MENU</a><a style="width:118px">WINE LIST</a><a style="width:105px">GALLERY</a><a style="width:157px">LARKSPUR COURT</a><a style="flex:1">CONTACT US</a>
  </nav>
  <div class="hero" role="img" aria-label="Platter of grilled seafood with lobster, prawns and salmon">
    <svg class="hero-arrow" style="left:32px" width="30" height="44" viewBox="0 0 30 44"><polyline points="26,2 6,22 26,42" fill="none" stroke="#555" stroke-width="5"/></svg>
    <svg class="hero-arrow" style="left:745px" width="30" height="44" viewBox="0 0 30 44"><polyline points="4,2 24,22 4,42" fill="none" stroke="#555" stroke-width="5"/></svg>
    <div class="hero-title">SEAFOOD DISHES</div>
    <div class="dots"><span></span><span class="on"></span><span></span><span></span></div>
  </div>

  <h2 class="heading" style="left:10px;top:595px">WELCOME TO OUR SITE</h2>
  <div class="welcome">
    <p>Chef Wen is named after its' executive chef, Mr Wen. Chef Wen had been in his career for nearly two decades before he moved to Australia 9 years ago. He settled in Adelaide then started his first restaurant, Larkspur Court, in Ashgrove. Larkspur Court has been running successfully for years due to Chef Wen's talent of cooking.</p>
    <p>To be able to provide pure Chinese tea, Chef Wen sources genuin high quality tea leaves and courier to Australia by air, thus a wide range of choices are available to our guests.</p>
  </div>

  <h2 class="heading" style="left:7px;top:780px">OUR MENU</h2>
  <div class="tile" style="left:8px;top:799px;background:linear-gradient(135deg,#e8d6b0,#c9a36a)" role="img" aria-label="Scallop dumplings in a bamboo steamer"><div class="cap">SCALLOP DUMPLINGS</div></div>
  <div class="tile" style="left:265px;top:799px;background:linear-gradient(135deg,#b8523a,#e06a4a 50%,#f0e2d8)" role="img" aria-label="Frozen crab on a white plate"><div class="cap">FROZEN CRAB</div></div>
  <div class="tile" style="left:8px;top:948px;background:radial-gradient(circle at 50% 45%,#f0a040,#d9601e 60%,#b8400e)" role="img" aria-label="Abalone noodles in sauce"><div class="cap">ABALONE NOODLES</div></div>
  <div class="tile" style="left:265px;top:948px;background:linear-gradient(135deg,#f2eae4,#e8a59a 50%,#f4ede8)" role="img" aria-label="Steamed whole coral trout with ginger and shallots"><div class="cap">STEAMED WHOLE CORAL TROUT<br>WITH GNGER &amp; SHALLOTS</div></div>
  <div class="view-all">VIEW OUR MENU ITEMS</div>

  <h2 class="heading" style="left:535px;top:596px">TRADING HOURS</h2>
  <div class="hours">
    <div class="open-box">We are open 7 days</div>
    <div><b>Lunch</b></div>
    <div>Monday to <span class="hl">Friday 11:30am - 2:30pm</span></div>
    <div>Saturday to <span class="hl">Sunday 11:00am - 3:00pm</span></div>
    <hr>
    <div><b>Dinner</b></div>
    <div>Monday to Sunday <span class="hl">6:00pm</span> Until Late</div>
  </div>

  <div class="location">
    <h3>LOCATION</h3>
    <div class="map" role="img" aria-label="Street map showing the restaurant location">
      <svg width="18" height="28" viewBox="0 0 18 28"><path d="M9 27 C9 27 1 15 1 9 A8 8 0 0 1 17 9 C17 15 9 27 9 27Z" fill="#e53935" stroke="#a11" stroke-width="1"/><circle cx="9" cy="9" r="3" fill="#8b0f0f"/></svg>
    </div>
    <div class="addr">3/88 KENDRICK ROAD<br>ELM HOLLOW, SA, 5070</div>
  </div>
</div>

<footer class="footer">
  <div class="follow">FOLLOW US ON</div>
  <div class="social"><span></span><span></span><span></span></div>
  <div class="fnav">HOME &nbsp;| &nbsp;ABOUT US &nbsp;| &nbsp;MENU &nbsp;| &nbsp;WINE LIST &nbsp;| &nbsp;GALLERY &nbsp;| &nbsp;CONTACT US &nbsp;| &nbsp;LARKSPUR COURT</div>
  <div class="copy">COPYRIGHTS @ 2014 ALL RIGHTS RESERVED</div>
</footer>
</body>
</html>
```